Classy, Elegant, Simple Business Card Design

Looking to have a classy, simple, and elegant design. Want a top notch designed business card. I really like the look of the new torvane credit card. I also like the design I attached. I am trying to reach 21-29 year old females for booking us for there wedding or event. We offer Disc Jockey Service, Photo Booth Rentals, and Uplighting .

Target Market(s)

21-28 year old females

Contact Information for Business Card

Has to have logo, website, email, and phone number

Font styles to use
Other font styles liked:
• open to font choice, modern, clean
Designer to choose
33a6d7
0791cd
0555a3
ffffff

Requirements
Must have
• Has to have logo, website, email, and phone number
Nice to have
• I really like the design of the new torvane credit card. I also included my logo and some designs I like
Should not have
• clutter or too much info

```html
<!DOCTYPE html>
<html lang="en">
<head>
<meta charset="utf-8">
<title>Tidal Note Events – Business Card</title>
<link rel="stylesheet" href="https://fonts.googleapis.com/css2?family=Poppins:wght@400;500;600&display=swap">
<style>
  :root {
    --page-bg: #dfe2e5;
    --card-top: #f3f4f5;
    --card-bottom: #e6e9eb;
    --navy: #0555a3;
    --blue: #0791cd;
    --sky: #33a6d7;
    --name-blue: #2a6fae;
    --grey-text: #8a8c8e;
    --ink: #1f2326;
    --icon-cut: #eef0f1;
  }
  * { margin: 0; padding: 0; box-sizing: border-box; }
  html, body {
    width: 1200px;
    height: 969px;
    overflow: hidden;
    background: var(--page-bg);
    font-family: "Poppins", sans-serif;
  }
  .business-card {
    position: absolute;
    left: 100px;
    top: 199px;
    width: 1000px;
    height: 571px;
    background: linear-gradient(160deg, var(--card-top), var(--card-bottom));
    border: 1px solid #c9cdd1;
    overflow: hidden;
  }
  .decor-band {
    position: absolute;
    left: 0;
    right: 0;
    top: 232px;
    height: 100px;
    background: linear-gradient(90deg, rgba(5, 85, 163, 0.55), rgba(7, 145, 205, 0.45), rgba(5, 85, 163, 0.55));
  }
  .brand {
    position: absolute;
    right: 80px;
    top: 176px;
    display: flex;
    align-items: center;
    gap: 14px;
  }
  .brand-dot {
    width: 18px;
    height: 18px;
    border-radius: 50%;
    background: var(--navy);
  }
  .brand-name {
    font-size: 34px;
    font-weight: 600;
    color: var(--navy);
    letter-spacing: 0.5px;
  }
  .person {
    position: absolute;
    left: 62px;
    top: 344px;
  }
  .person-name {
    font-size: 33px;
    font-weight: 500;
    color: var(--name-blue);
    line-height: 1.2;
  }
  .person-role {
    font-size: 22px;
    color: var(--grey-text);
    line-height: 1.3;
  }
  .contact-list, .service-list {
    position: absolute;
    top: 437px;
    list-style: none;
  }
  .contact-list { left: 70px; }
  .service-list { left: 675px; }
  .contact-list li, .service-list li {
    display: flex;
    align-items: center;
    height: 29px;
    font-size: 22px;
    color: var(--ink);
  }
  .contact-list li { color: #4b4f53; }
  .contact-icon {
    width: 20px;
    height: 20px;
    margin-right: 13px;
    fill: var(--name-blue);
  }
  .service-list li::before {
    content: "";
    width: 6px;
    height: 6px;
    border-radius: 50%;
    background: var(--navy);
    margin-right: 12px;
  }
</style>
</head>
<body>
  <div class="business-card">
    <div class="decor-band" role="img" aria-label="Decorative flowing blue wave band across the card"></div>

    <div class="brand">
      <span class="brand-dot"></span>
      <span class="brand-name">Tidal Note Events</span>
    </div>

    <div class="person">
      <p class="person-name">Daniel Reyes</p>
      <p class="person-role">President</p>
    </div>

    <ul class="contact-list">
      <li>
        <svg class="contact-icon" viewBox="0 0 24 24" aria-hidden="true"><path d="M6.6 10.8a15.1 15.1 0 0 0 6.6 6.6l2.2-2.2a1 1 0 0 1 1-.25 11.4 11.4 0 0 0 3.6.57 1 1 0 0 1 1 1V20a1 1 0 0 1-1 1A17 17 0 0 1 3 4a1 1 0 0 1 1-1h3.5a1 1 0 0 1 1 1c0 1.25.2 2.45.57 3.57a1 1 0 0 1-.25 1z"/></svg>
        555-204-7731
      </li>
      <li>
        <svg class="contact-icon" viewBox="0 0 24 24" aria-hidden="true"><rect x="3" y="5" width="18" height="14"/><path d="M3.5 6l8.5 6.6L20.5 6" fill="none" stroke="var(--icon-cut)" stroke-width="1.6"/></svg>
        hello@tidalnoteevents.com
      </li>
      <li>
        <svg class="contact-icon" viewBox="0 0 24 24" aria-hidden="true"><circle cx="12" cy="12" r="9.5"/><path d="M3 12h18M12 3c3 3 3 15 0 18M12 3c-3 3-3 15 0 18" fill="none" stroke="var(--icon-cut)" stroke-width="1.4"/></svg>
        www.tidalnoteevents.com
      </li>
    </ul>

    <ul class="service-list">
      <li>Disc Jockey Service</li>
      <li>Photo Booth Rentals</li>
      <li>Uplighting</li>
    </ul>
  </div>
</body>
</html>
```